Take your idea to next level of implementation

Need a website for the training program that we are launching. Lantern on Hill is training provided to aspiring entrepreneurs.
The training comprises of business skills imparted to participants in order to help them develop their ideas and take the ideas to the next level of implementation.
The training program will be conducted in 8 sessions spanning over 5 months.

Coding

Coded - Design and coding required

Number of Pages Required

1 page

Colors

Designer to choose colors to be used in the design.

Requirements
Must have
• The project must have single page
Nice to have
• It would be nice to have a landing page that feels positive and will attract applicants.
• It should be highly professional.
Should not have
• Pictures used in the template should not have any people.

```html
<!DOCTYPE html>
<html lang="en">
<head>
<meta charset="utf-8">
<title>Lantern on Hill – Landing Page Variants</title>
<link rel="stylesheet" href="https://fonts.googleapis.com/css2?family=Lato:wght@300;400;700;900&family=Roboto:ital,wght@0,400;0,500;0,700;1,400;1,700&display=swap">
<style>
:root{
  --sheet:#8e8e8e;
  --navy:#1d3a70;
  --navy-deep:#1a2f5c;
  --blue:#3b7fcb;
  --blue-bright:#4a90d4;
  --pale:#dbe8f7;
  --ink:#222a38;
  --text:#7a7f88;
  --bar:#242424;
  --mist:#f3f4f7;
  --white:#fff;
}
*{box-sizing:border-box;margin:0;padding:0}
html,body{width:1200px;height:2410px;overflow:hidden;background:var(--sheet)}
body{font-family:"Roboto",Arial,sans-serif;color:var(--text)}
.sheet{position:relative;width:1200px;height:2410px;background:var(--sheet)}
.page{position:absolute;top:31px;width:561px;height:2337px;background:var(--white);overflow:hidden;border-top:2px solid var(--blue-bright)}
.page--a{left:28px}
.page--b{left:611px}
section{position:relative;overflow:hidden}
h2.title{font-family:"Lato",sans-serif;font-size:16px;font-weight:300;color:var(--navy);letter-spacing:.2px}
h2.title b{font-weight:900}
h2.title.underlined::after{content:"";display:block;width:24px;height:2px;background:var(--navy);margin-top:3px}
p{font-size:6.4px;line-height:1.85}
.pill{display:inline-flex;align-items:center;gap:4px;border-radius:12px;font-family:"Lato",sans-serif;font-weight:700;font-size:6.5px;padding:6px 10px;letter-spacing:.2px}
.pill--blue{background:var(--blue);color:var(--white)}
.pill--white{background:var(--white);color:var(--blue)}
.pill i{width:7px;height:7px;border-radius:50%;background:currentColor;display:inline-block;position:relative}
.pill i::after{content:"";position:absolute;left:2px;top:2px;border:1.5px solid transparent;border-left-color:var(--white)}
.pill--white i::after{border-left-color:var(--white)}

/* header */
.masthead{height:42px;display:flex;align-items:center;justify-content:space-between;padding:0 52px 0 52px}
.brand{display:flex;align-items:center;gap:5px;font-family:"Lato",sans-serif;font-weight:900;font-size:8px;line-height:.95;color:var(--navy);letter-spacing:.3px}
.brand span.mark{width:18px;height:18px;border-radius:50%;border:1.5px solid var(--navy)}
.nav{display:flex;gap:16px;font-family:"Roboto",sans-serif;font-size:6.4px;font-weight:500;color:var(--ink);margin-right:20px}
.nav .active{color:var(--blue);position:relative}
.nav .active::before{content:"";position:absolute;left:4px;top:-10px;width:6px;height:6px;border-radius:50%;border:1px solid var(--blue)}

/* hero */
.hero{height:238px;color:var(--white)}
.hero--photo{background:linear-gradient(120deg,#2c5aa8 0%,#3f77c4 45%,#2d5ca8 100%);text-align:center}
.hero--photo .veil{position:absolute;inset:0;background:radial-gradient(ellipse at 25% 80%,rgba(20,45,100,.45),transparent 60%)}
.hero h1{font-family:"Lato",sans-serif;font-weight:900;font-size:22px;letter-spacing:-.2px}
.hero .lede{font-size:7.6px;line-height:1.7;font-weight:500}
.hero--photo .inner{position:relative;padding-top:60px}
.hero--photo .lede{margin-top:10px}
.play{width:32px;height:32px;border-radius:50%;border:2px solid var(--white);margin:18px auto 0;position:relative}
.play::after{content:"";position:absolute;left:12px;top:8px;border:7px solid transparent;border-left:10px solid var(--white);border-right:0}
.hero--scene{background:linear-gradient(100deg,#1f4da3 0%,#2f6dc7 50%,#3d86d8 100%)}
.hero--scene .art{position:absolute;right:0;top:0;width:290px;height:238px;background:radial-gradient(ellipse at 60% 55%,rgba(220,235,255,.55),rgba(80,140,220,.2) 55%,transparent 75%)}
.hero--scene .inner{position:absolute;left:52px;top:72px;width:260px}
.hero--scene .lede{margin-top:12px}
.hero--scene .pill{margin-top:12px;font-size:7.5px;padding:7px 12px}

/* about */
.about{height:316px}
.about .copy{position:absolute;left:52px;top:64px;width:232px}
.about .copy p{margin-top:6px}
.about .copy h2{margin-bottom:8px}
.about strong{color:var(--navy);font-weight:700}
.about a{color:var(--blue);font-weight:700;text-decoration:underline}
.about .cta-head{font-size:6.8px;font-weight:700;color:var(--ink);margin-top:12px}
.about .pill{margin-top:16px}
.halo{position:absolute;border-radius:50%;background:var(--pale)}
.photo-disc{position:absolute;border-radius:50%}
.about .halo{left:338px;top:40px;width:236px;height:236px}
.about .photo-disc{left:316px;top:64px;width:186px;height:186px;background:radial-gradient(circle at 50% 35%,#f4d9a6 0%,#b98d5e 35%,#5b4a3d 75%)}

/* band */
.freebar{height:26px;background:var(--bar);color:var(--white);font-family:"Roboto",sans-serif;font-weight:500;font-size:7.6px;display:flex;align-items:center;justify-content:center}
.features{height:144px;background:linear-gradient(90deg,#1f3f7a,#2d5ea9 55%,#3f83cd);display:flex;justify-content:space-between;padding:22px 52px 0;color:var(--white);text-align:center}
.feature{width:140px}
.feature svg{height:30px;width:30px;display:block;margin:0 auto}
.feature h3{font-family:"Roboto",sans-serif;font-size:7.6px;font-weight:500;margin-top:8px}
.feature p{font-size:6.2px;line-height:1.8;margin-top:8px;color:#e8eef9}

/* programme */
.programme{height:334px}
.programme .halo{left:-60px;top:50px;width:250px;height:250px}
.programme .photo-disc{left:54px;top:84px;width:190px;height:190px;background:radial-gradient(circle at 45% 45%,#f3f1ec 0%,#d8d2c6 45%,#8d8478 90%)}
.programme .copy{position:absolute;left:280px;top:50px;width:228px}
.programme .ask{font-size:6.8px;font-weight:500;color:var(--ink);line-height:1.75;margin-top:10px}
.programme .copy p{margin-top:6px}
.programme strong{color:var(--navy)}

/* why */
.why{height:190px;background:var(--mist)}
.why .copy{position:absolute;left:72px;top:36px;width:258px}
.why .copy p{margin-top:20px;text-align:justify}
.why .bulb{position:absolute;left:365px;top:10px;width:124px;height:170px;border-radius:62px 62px 30px 30px;background:radial-gradient(circle at 50% 38%,rgba(58,127,203,.35),rgba(34,160,150,.15) 55%,transparent 72%)}

/* faqs */
.faqs{height:308px}
.faqs h2{text-align:center;padding-top:38px}
.faq-grid{position:absolute;left:52px;top:78px;width:457px;display:flex;justify-content:space-between}
.faq-col{width:219px;display:flex;flex-direction:column;gap:5px}
.faq{min-height:21px;border:1px solid #e4e6ea;display:flex;align-items:center;justify-content:space-between;padding:4px 6px;font-size:6.1px;line-height:1.6;color:#555b65}
.faq::after{content:"";flex:0 0 6px;height:6px;border-radius:50%;background:#3a3f48;margin-left:6px}
.faq.open{background:var(--blue-bright);border-color:var(--blue-bright);color:var(--white);display:block;padding:5px 6px}
.faq.open::after{display:none}
.faq.open .q{display:flex;justify-content:space-between;font-weight:500}
.faq.open .q::after{content:"";width:6px;height:6px;border-radius:50%;background:var(--white)}
.faq.open .a{font-size:5.8px;margin-top:4px;color:#eef4fc}

/* academic */
.academic{height:152px;background:linear-gradient(90deg,#2b5aa4,#3e7fcb 55%,#3170bc);color:var(--white);text-align:center}
.academic h2{color:var(--white);padding-top:20px;font-size:16px}
.academic p{width:420px;margin:8px auto 0;font-size:6.4px;color:#eaf0fa}
.academic .note{font-weight:700;margin-top:8px;color:var(--white)}
.partners{display:flex;justify-content:center;gap:22px;margin-top:8px}
.partner{width:86px;height:33px;background:var(--white);display:flex;align-items:center;justify-content:center;font-family:"Roboto",sans-serif;font-weight:700;font-size:7.5px;color:var(--navy)}

/* people */
.people{height:232px}
.people h2{text-align:center;padding-top:38px}
.team{position:absolute;left:44px;top:73px;width:474px;display:flex;justify-content:space-between}
.member{width:92px;text-align:center}
.member .portrait{width:66px;height:66px;border-radius:50%;margin:0 auto;background:linear-gradient(160deg,#c9d7e6,#8a9cb2);position:relative}
.member .portrait.alt{background:linear-gradient(160deg,#aad6ee,#5fa1d2)}
.member .portrait::after{content:"";position:absolute;left:25px;bottom:-6px;width:16px;height:16px;border-radius:50%;background:var(--blue);border:2px solid var(--white)}
.member h4{font-family:"Roboto",sans-serif;font-size:7.4px;font-weight:500;color:var(--ink);margin-top:14px}
.member .role{font-size:5.9px;font-style:italic;color:#6f83a6;line-height:1.6;margin-top:4px}
.member .org{font-size:5.9px;font-style:italic;font-weight:700;color:var(--ink);margin-top:3px}

/* apply */
.apply{height:209px;background:var(--mist);text-align:center}
.apply .kicker{font-size:7.6px;color:var(--blue);padding-top:14px}
.apply h2{font-size:16px;margin-top:2px}
.apply p{font-size:6.4px;color:#555b65;line-height:1.9;margin-top:8px}
.contacts{display:flex;justify-content:space-between;width:440px;margin:14px auto 0;text-align:left}
.contact{display:flex;gap:7px;align-items:center}
.contact .ico{width:31px;height:31px;border-radius:50%;background:var(--pale);display:flex;align-items:center;justify-content:center}
.contact .ico span{width:23px;height:23px;border-radius:50%;background:var(--blue-bright);display:flex;align-items:center;justify-content:center}
.contact h5{font-family:"Roboto",sans-serif;font-size:7.2px;font-weight:500;color:var(--ink)}
.contact small{font-size:6px;color:#6a707a}
.contact .big{font-size:7.2px;color:var(--ink)}
.footer{height:146px;background:var(--navy-deep)}
.footer .legal{position:absolute;left:86px;bottom:18px;font-size:6.2px;color:var(--white)}
.footer .social{position:absolute;right:84px;bottom:13px;display:flex;gap:4px}
.footer .social span{width:17px;height:17px;border-radius:50%;border:1px solid var(--white)}
.form-card{position:absolute;left:86px;top:2136px;width:389px;height:160px;background:var(--blue-bright);color:var(--white)}
.form-card .label{position:absolute;left:32px;top:36px;width:44px;text-align:center;font-family:"Lato",sans-serif;font-size:13px;line-height:1.25;font-weight:400}
.form-card .label svg{display:block;margin:0 auto 8px}
.fields{position:absolute;left:113px;top:40px;width:265px;display:grid;grid-template-columns:1fr 1fr;column-gap:16px;row-gap:10px}
.field{border-bottom:1px solid rgba(255,255,255,.85);font-size:5.9px;padding:0 3px 5px}
.submit{position:absolute;left:215px;top:112px;width:72px;height:21px;border-radius:11px;background:var(--white);color:var(--navy);font-family:"Roboto",sans-serif;font-weight:700;font-size:6.6px;display:flex;align-items:center;justify-content:center}
</style>
</head>
<body>
<div class="sheet">

<!-- ============ Variant A ============ -->
<div class="page page--a">
  <header class="masthead">
    <div class="brand"><span class="mark"></span><div>LANTERN ON<br>HILL</div></div>
    <nav class="nav"><span class="active">About</span><span>Programme</span><span>Why LOH</span><span>FAQs</span><span>Academic Support</span><span>Apply</span></nav>
  </header>

  <section class="hero hero--photo" role="img" aria-label="Blue-toned photo of hands working on a laptop">
    <div class="veil"></div>
    <div class="inner">
      <h1>LANTERN ON HILL</h1>
      <div class="lede">Lantern On Hill Is A Project Delivered By Northbridge School Of<br>Business, In Partnership With Valmont University.</div>
      <div class="play"></div>
    </div>
  </section>

  <section class="about">
    <div class="halo"></div>
    <div class="photo-disc" role="img" aria-label="Photo of a glowing light bulb above a notebook and laptop"></div>
    <div class="copy">
      <h2 class="title underlined"><b>ABOUT</b> US</h2>
      <p>Lantern On Hill Is A Project Delivered By <strong>NORTHBRIDGE SCHOOL OF BUSINESS</strong>, In Partnership With <strong>VALMONT UNIVERSITY</strong>. This Project Is First Of Its Kind Training Programme To Aspiring Entrepreneurs.</p>
      <p>The first round of applications is open till <strong>1st MARCH, 2020</strong>. If you would like <strong>to be part of the training and to be informed</strong> further please <a>Fill in the Form Below.</a></p>
      <div class="cta-head">TO APPLY FOR THE FIRST EDITION OF THIS PROJECT,</div>
      <p style="margin-top:2px">Please Click Below And Fill In Details To Express Your Interest</p>
      <span class="pill pill--blue">APPLY NOW <i></i></span>
    </div>
  </section>

  <div class="freebar">THE TRAINING IS COMPLETELY FREE OF CHARGE</div>
  <section class="features">
    <div class="feature">
      <svg viewBox="0 0 30 30" fill="#fff"><circle cx="15" cy="6" r="3"/><circle cx="15" cy="15" r="3.5"/><path d="M8 28c0-6 3-9 7-9s7 3 7 9z"/></svg>
      <h3>LOREM IPSUM DOLOR</h3>
      <p>Sed ut perspiciatis unde omnis iste natus error sit voluptatem doloremque laudantium, totam rem eaque ipsa</p>
    </div>
    <div class="feature">
      <svg viewBox="0 0 30 30"><path d="M8 24a6 6 0 0 1 0-12 8 8 0 0 1 15 2 5 5 0 0 1-1 10z" fill="#fff"/><rect x="11" y="16" width="2" height="6" fill="#2d5ea9"/><rect x="15" y="13" width="2" height="9" fill="#2d5ea9"/><rect x="19" y="17" width="2" height="5" fill="#2d5ea9"/></svg>
      <h3>LOREM IPSUM DOLOR</h3>
      <p>Sed ut perspiciatis unde omnis iste natus error sit voluptatem doloremque laudantium, totam rem eaque ipsa</p>
    </div>
    <div class="feature">
      <svg viewBox="0 0 30 30" fill="none" stroke="#fff" stroke-width="1.5"><rect x="9" y="2" width="12" height="26" rx="2"/><path d="M12 20v-4M15 20v-7M18 20v-5"/></svg>
      <h3>LOREM IPSUM DOLOR</h3>
      <p>Sed ut perspiciatis unde omnis iste natus error sit voluptatem doloremque laudantium, totam rem eaque ipsa</p>
    </div>
  </section>

  <section class="programme">
    <div class="halo"></div>
    <div class="photo-disc" role="img" aria-label="Photo of a desk with laptop, charts and glasses seen from above"></div>
    <div class="copy">
      <h2 class="title underlined"><b>OUR</b> PROGRAMME</h2>
      <div class="ask">So, you have an idea?<br>What next?</div>
      <p>Be a part of Lantern on Hill! This training program will support your efforts to take your idea closer to implementation. As part of the project, aspiring entrepreneurs will receive a <strong>five-month support programme</strong>.</p>
      <p>Our dynamic and engaging approach will strengthen your resolve and provide you with tools required to implement your idea. The training programme will aid development of management skills required to kickstart your entrepreneurial endeavour.</p>
      <p>Throughout the course, you will be following tried and tested rigorous methodologies developed in partnership with academics and business experts in management.</p>
      <p>The project will use interactive and hands on materials. Training will be delivered by experts and to small groups to enable you to take the leap, right from the first session.</p>
    </div>
  </section>

  <section class="why">
    <div class="copy">
      <h2 class="title underlined"><b>WHY LANTERN ON</b> HILL?</h2>
      <p>Participants who successfully complete the programme will receive a certificate of participation. They will also be invited to dedicated exclusive monthly events and networking opportunities. Successful participants may also apply to participate in Lantern on Hill's annual Investor Demo Day, which will be scheduled towards the end of 2020. Lantern on Hill training is offered free of charge as part of a research programme.</p>
    </div>
    <div class="bulb" role="img" aria-label="Illustration of a light bulb made of connected science and business icons"></div>
  </section>

  <section class="faqs">
    <h2 class="title"><b>FAQs</b></h2>
    <div class="faq-grid">
      <div class="faq-col">
        <div class="faq">What is the structure of training program?</div>
        <div class="faq">When and where is the Lantern on Hill training offered?</div>
        <div class="faq">What is the fee for the training programme?</div>
        <div class="faq">What is the content of training program?</div>
        <div class="faq">Is it compulsory to attend all sessions?</div>
        <div class="faq">What is the class size?</div>
        <div class="faq">Will I be asked to share confidentially information with the other members of my class?</div>
      </div>
      <div class="faq-col">
        <div class="faq">I do not live in Riverton, so how about travel &amp; accommodation?</div>
        <div class="faq">Who are going to be the instructors/facilitators for the business support programme?</div>
        <div class="faq open"><div class="q">Who are eligible to join the programme?</div><div class="a">Aspiring entrepreneurs who have an idea and would like to take further steps towards implementation are welcome to join our training program.</div></div>
        <div class="faq">What is the main purpose of the entrepreneur training programme</div>
        <div class="faq">Is participation in the business support programme only open to founders and co-founders?</div>
        <div class="faq">How will the data be used and their security be protected?</div>
      </div>
    </div>
  </section>

  <section class="academic">
    <h2 class="title"><b>ACADEMIC</b> SUPPORT</h2>
    <p>Northbridge School of Business, in collaboration with Valmont University, will provide their world-renowned expertise in the field of management and entrepreneurship to deliver cutting-edge business knowledge to aspiring entrepreneurs with ideas in nascent phase.</p>
    <p class="note">The programme is free of charge!</p>
    <div class="partners"><div class="partner">Northbridge</div><div class="partner">Valmont</div></div>
  </section>

  <section class="people">
    <h2 class="title"><b>OUR</b> PEOPLE</h2>
    <div class="team">
      <div class="member"><div class="portrait" role="img" aria-label="Portrait photo"></div><h4>Arun Mehta</h4><div class="role">Associate Professor of<br>Strategy &amp; Entrepreneurship</div><div class="org">Northbridge School of Business</div></div>
      <div class="member"><div class="portrait alt" role="img" aria-label="Portrait photo"></div><h4>Kavya Rao</h4><div class="role">Assistant Professor of<br>Entrepreneurship</div><div class="org">Northbridge School of Business</div></div>
      <div class="member"><div class="portrait" role="img" aria-label="Portrait photo"></div><h4>Marco Ferri</h4><div class="role">Professor of Business<br>Organization</div><div class="org">Valmont University</div></div>
      <div class="member"><div class="portrait" role="img" aria-label="Portrait photo"></div><h4>Luca Benassi</h4><div class="role">Professor of Management</div><div class="org">Valmont University</div></div>
      <div class="member"><div class="portrait" role="img" aria-label="Portrait photo"></div><h4>Elena Conti</h4><div class="role">Doctoral Candidate in<br>Management</div><div class="org">Valmont University</div></div>
    </div>
  </section>

  <section class="apply">
    <div class="kicker">Lantern on Hill</div>
    <h2 class="title"><b>HOW</b> TO APPLY</h2>
    <p>If you are interested in applying, to hear from us,<br>Please provide following details and we will reach out to you with further information</p>
    <div class="contacts">
      <div class="contact"><div class="ico"><span><svg width="12" height="9" viewBox="0 0 12 9" fill="none" stroke="#fff"><rect x=".5" y=".5" width="11" height="8"/><path d="M.5.5 6 5l5.5-4.5"/></svg></span></div><div><h5>Email Address</h5><small>contact@lanternonhill.com</small></div></div>
      <div class="contact"><div class="ico"><span><svg width="10" height="11" viewBox="0 0 10 11" fill="#fff"><path d="M2 0h3l1 3-2 1a6 6 0 0 0 3 3l1-2 3 1v3c0 1-1 2-2 2C4 11 0 7 0 2c0-1 1-2 2-2z"/></svg></span></div><div><h5>Let us give you a call</h5><div class="big">555-010-2040</div></div></div>
      <div class="contact"><div class="ico"><span><svg width="12" height="12" viewBox="0 0 12 12" fill="none" stroke="#fff" stroke-width="1.2"><circle cx="6" cy="6" r="5"/><path d="M6 3v3l2 1"/></svg></span></div><div><h5>Opening Hours</h5><small>Mon - Sat: 9Am - 8pm</small></div></div>
    </div>
  </section>
  <section class="footer">
    <div class="legal">Copyright 2019 Lantern on Hill | All Rights Reserved.</div>
    <div class="social"><span></span><span></span><span></span></div>
  </section>
  <div class="form-card">
    <div class="label"><svg width="42" height="28" viewBox="0 0 42 28" fill="none" stroke="#fff" stroke-width="1.6"><rect x="1" y="1" width="40" height="26"/><path d="M1 1l20 15L41 1M1 27l14-14M41 27 27 13"/></svg>APPLY<br>NOW</div>
    <div class="fields"><div class="field">Name*</div><div class="field">Surname*</div><div class="field">Your Phone*</div><div class="field">Your Email*</div></div>
    <div class="submit">SUBMIT</div>
  </div>
</div>

<!-- ============ Variant B ============ -->
<div class="page page--b">
  <header class="masthead">
    <div class="brand"><span class="mark"></span><div>LANTERN ON<br>HILL</div></div>
    <nav class="nav"><span class="active">About</span><span>Programme</span><span>Why LOH</span><span>FAQs</span><span>Academic Support</span><span>Apply</span></nav>
  </header>

  <section class="hero hero--scene">
    <div class="art" role="img" aria-label="Illustration of blue stairs with a lightbulb and gear, rising to an arrow over a world map and chart"></div>
    <div class="inner">
      <h1>LANTERN ON HILL</h1>
      <div class="lede">Lantern On Hill Is A Project Delivered By Northbridge School Of Business, In Partnership With Valmont University.</div>
      <span class="pill pill--white">APPLY NOW <i></i></span>
    </div>
  </section>

  <section class="about">
    <div class="halo"></div>
    <div class="photo-disc" role="img" aria-label="Photo of a glowing light bulb above a notebook and laptop"></div>
    <div class="copy">
      <h2 class="title underlined"><b>ABOUT</b> US</h2>
      <p>Lantern On Hill Is A Project Delivered By <strong>NORTHBRIDGE SCHOOL OF BUSINESS</strong>, In Partnership With <strong>VALMONT UNIVERSITY</strong>. This Project Is First Of Its Kind Training Programme To Aspiring Entrepreneurs.</p>
      <p>The first round of applications is open till <strong>1st MARCH, 2020</strong>. If you would like <strong>to be part of the training and to be informed</strong> further please <a>Fill in the Form Below.</a></p>
      <div class="cta-head">TO APPLY FOR THE FIRST EDITION OF THIS PROJECT,</div>
      <p style="margin-top:2px">Please Click Below And Fill In Details To Express Your Interest</p>
      <span class="pill pill--blue">APPLY NOW <i></i></span>
    </div>
  </section>

  <div class="freebar">THE TRAINING IS COMPLETELY FREE OF CHARGE</div>
  <section class="features">
    <div class="feature">
      <svg viewBox="0 0 30 30" fill="#fff"><circle cx="15" cy="6" r="3"/><circle cx="15" cy="15" r="3.5"/><path d="M8 28c0-6 3-9 7-9s7 3 7 9z"/></svg>
      <h3>LOREM IPSUM DOLOR</h3>
      <p>Sed ut perspiciatis unde omnis iste natus error sit voluptatem doloremque laudantium, totam rem eaque ipsa</p>
    </div>
    <div class="feature">
      <svg viewBox="0 0 30 30"><path d="M8 24a6 6 0 0 1 0-12 8 8 0 0 1 15 2 5 5 0 0 1-1 10z" fill="#fff"/><rect x="11" y="16" width="2" height="6" fill="#2d5ea9"/><rect x="15" y="13" width="2" height="9" fill="#2d5ea9"/><rect x="19" y="17" width="2" height="5" fill="#2d5ea9"/></svg>
      <h3>LOREM IPSUM DOLOR</h3>
      <p>Sed ut perspiciatis unde omnis iste natus error sit voluptatem doloremque laudantium, totam rem eaque ipsa</p>
    </div>
    <div class="feature">
      <svg viewBox="0 0 30 30" fill="none" stroke="#fff" stroke-width="1.5"><rect x="9" y="2" width="12" height="26" rx="2"/><path d="M12 20v-4M15 20v-7M18 20v-5"/></svg>
      <h3>LOREM IPSUM DOLOR</h3>
      <p>Sed ut perspiciatis unde omnis iste natus error sit voluptatem doloremque laudantium, totam rem eaque ipsa</p>
    </div>
  </section>

  <section class="programme">
    <div class="halo"></div>
    <div class="photo-disc" role="img" aria-label="Photo of a desk with laptop, charts and glasses seen from above"></div>
    <div class="copy">
      <h2 class="title underlined"><b>OUR</b> PROGRAMME</h2>
      <div class="ask">So, you have an idea?<br>What next?</div>
      <p>Be a part of Lantern on Hill! This training program will support your efforts to take your idea closer to implementation. As part of the project, aspiring entrepreneurs will receive a <strong>five-month support programme</strong>.</p>
      <p>Our dynamic and engaging approach will strengthen your resolve and provide you with tools required to implement your idea. The training programme will aid development of management skills required to kickstart your entrepreneurial endeavour.</p>
      <p>Throughout the course, you will be following tried and tested rigorous methodologies developed in partnership with academics and business experts in management.</p>
      <p>The project will use interactive and hands on materials. Training will be delivered by experts and to small groups to enable you to take the leap, right from the first session.</p>
    </div>
  </section>

  <section class="why">
    <div class="copy">
      <h2 class="title underlined"><b>WHY LANTERN ON</b> HILL?</h2>
      <p>Participants who successfully complete the programme will receive a certificate of participation. They will also be invited to dedicated exclusive monthly events and networking opportunities. Successful participants may also apply to participate in Lantern on Hill's annual Investor Demo Day, which will be scheduled towards the end of 2020. Lantern on Hill training is offered free of charge as part of a research programme.</p>
    </div>
    <div class="bulb" role="img" aria-label="Illustration of a light bulb made of connected science and business icons"></div>
  </section>

  <section class="faqs">
    <h2 class="title"><b>FAQs</b></h2>
    <div class="faq-grid">
      <div class="faq-col">
        <div class="faq">What is the structure of training program?</div>
        <div class="faq">When and where is the Lantern on Hill training offered?</div>
        <div class="faq">What is the fee for the training programme?</div>
        <div class="faq">What is the content of training program?</div>
        <div class="faq">Is it compulsory to attend all sessions?</div>
        <div class="faq">What is the class size?</div>
        <div class="faq">Will I be asked to share confidentially information with the other members of my class?</div>
      </div>
      <div class="faq-col">
        <div class="faq">I do not live in Riverton, so how about travel &amp; accommodation?</div>
        <div class="faq">Who are going to be the instructors/facilitators for the business support programme?</div>
        <div class="faq open"><div class="q">Who are eligible to join the programme?</div><div class="a">Aspiring entrepreneurs who have an idea and would like to take further steps towards implementation are welcome to join our training program.</div></div>
        <div class="faq">What is the main purpose of the entrepreneur training programme</div>
        <div class="faq">Is participation in the business support programme only open to founders and co-founders?</div>
        <div class="faq">How will the data be used and their security be protected?</div>
      </div>
    </div>
  </section>

  <section class="academic">
    <h2 class="title"><b>ACADEMIC</b> SUPPORT</h2>
    <p>Northbridge School of Business, in collaboration with Valmont University, will provide their world-renowned expertise in the field of management and entrepreneurship to deliver cutting-edge business knowledge to aspiring entrepreneurs with ideas in nascent phase.</p>
    <p class="note">The programme is free of charge!</p>
    <div class="partners"><div class="partner">Northbridge</div><div class="partner">Valmont</div></div>
  </section>

  <section class="people">
    <h2 class="title"><b>OUR</b> PEOPLE</h2>
    <div class="team">
      <div class="member"><div class="portrait" role="img" aria-label="Portrait photo"></div><h4>Arun Mehta</h4><div class="role">Associate Professor of<br>Strategy &amp; Entrepreneurship</div><div class="org">Northbridge School of Business</div></div>
      <div class="member"><div class="portrait alt" role="img" aria-label="Portrait photo"></div><h4>Kavya Rao</h4><div class="role">Assistant Professor of<br>Entrepreneurship</div><div class="org">Northbridge School of Business</div></div>
      <div class="member"><div class="portrait" role="img" aria-label="Portrait photo"></div><h4>Marco Ferri</h4><div class="role">Professor of Business<br>Organization</div><div class="org">Valmont University</div></div>
      <div class="member"><div class="portrait" role="img" aria-label="Portrait photo"></div><h4>Luca Benassi</h4><div class="role">Professor of Management</div><div class="org">Valmont University</div></div>
      <div class="member"><div class="portrait" role="img" aria-label="Portrait photo"></div><h4>Elena Conti</h4><div class="role">Doctoral Candidate in<br>Management</div><div class="org">Valmont University</div></div>
    </div>
  </section>

  <section class="apply">
    <div class="kicker">Lantern on Hill</div>
    <h2 class="title"><b>HOW</b> TO APPLY</h2>
    <p>If you are interested in applying, to hear from us,<br>Please provide following details and we will reach out to you with further information</p>
    <div class="contacts">
      <div class="contact"><div class="ico"><span><svg width="12" height="9" viewBox="0 0 12 9" fill="none" stroke="#fff"><rect x=".5" y=".5" width="11" height="8"/><path d="M.5.5 6 5l5.5-4.5"/></svg></span></div><div><h5>Email Address</h5><small>contact@lanternonhill.com</small></div></div>
      <div class="contact"><div class="ico"><span><svg width="10" height="11" viewBox="0 0 10 11" fill="#fff"><path d="M2 0h3l1 3-2 1a6 6 0 0 0 3 3l1-2 3 1v3c0 1-1 2-2 2C4 11 0 7 0 2c0-1 1-2 2-2z"/></svg></span></div><div><h5>Let us give you a call</h5><div class="big">555-010-2040</div></div></div>
      <div class="contact"><div class="ico"><span><svg width="12" height="12" viewBox="0 0 12 12" fill="none" stroke="#fff" stroke-width="1.2"><circle cx="6" cy="6" r="5"/><path d="M6 3v3l2 1"/></svg></span></div><div><h5>Opening Hours</h5><small>Mon - Sat: 9Am - 8pm</small></div></div>
    </div>
  </section>
  <section class="footer">
    <div class="legal">Copyright 2019 Lantern on Hill | All Rights Reserved.</div>
    <div class="social"><span></span><span></span><span></span></div>
  </section>
  <div class="form-card">
    <div class="label"><svg width="42" height="28" viewBox="0 0 42 28" fill="none" stroke="#fff" stroke-width="1.6"><rect x="1" y="1" width="40" height="26"/><path d="M1 1l20 15L41 1M1 27l14-14M41 27 27 13"/></svg>APPLY<br>NOW</div>
    <div class="fields"><div class="field">Name*</div><div class="field">Surname*</div><div class="field">Your Phone*</div><div class="field">Your Email*</div></div>
    <div class="submit">SUBMIT</div>
  </div>
</div>

</div>
</body>
</html>
```